Coastline Premier Retreats Business Card Design

Design a business card for Coastline Premier Retreats. Look at the website for colors and reference. Card should have logo, name, title, office number, mobile number, email, URL and a tagline like, "Luxury Hotel & Resort Email Marketing" (This might change).

https://www.coastlinepremierretreats.example

The rest I will leave up to your imagination.

Contact Information for Business Card

Logo, name, title, office number, mobile number, email, URL and a tagline like, "Luxury Hotel & Resort Email Marketing" (This might change).

```html
<!DOCTYPE html>
<html lang="en">
<head>
<meta charset="utf-8">
<title>Coastline Premier Retreats – Business Card</title>
<link href="https://fonts.googleapis.com/css2?family=Arimo:wght@400;700&display=swap" rel="stylesheet">
<style>
  :root {
    --ink: #1b1b1b;
    --orange: #f07a22;
    --paper: #ffffff;
    --stage: #3a3634;
    --text: #111111;
  }
  * { box-sizing: border-box; margin: 0; padding: 0; }
  html, body {
    width: 1200px; height: 900px; overflow: hidden;
    background: var(--stage);
    font-family: "Arimo", Arial, sans-serif;
  }
  .canvas {
    width: 1200px; height: 900px;
    display: flex; flex-direction: column; align-items: center; justify-content: center;
    gap: 40px;
  }
  .card {
    position: relative;
    width: 665px; height: 380px;
    border-radius: 26px;
    overflow: hidden;
  }
  .card-back {
    background: var(--ink);
    display: flex; align-items: center; justify-content: center;
  }
  .brand-name {
    font-weight: 700;
    text-transform: uppercase;
    letter-spacing: 0.04em;
    line-height: 1.1;
  }
  .card-back .brand-name {
    color: var(--paper);
    font-size: 46px;
    text-align: center;
  }
  .card-front { background: var(--paper); }
  .swoosh { position: absolute; inset: 0; width: 100%; height: 100%; }
  .card-front .brand-name {
    position: absolute; left: 40px; top: 150px;
    color: var(--text);
    font-size: 21px;
  }
  .divider {
    position: absolute; left: 300px; top: 34px;
    width: 2px; height: 180px;
    background: var(--orange);
  }
  .details {
    position: absolute; left: 318px; top: 28px;
    color: var(--text);
  }
  .person-name {
    color: var(--orange);
    font-weight: 700;
    font-size: 24px;
    line-height: 1.2;
    text-transform: uppercase;
    margin-bottom: 4px;
  }
  .role { font-size: 15px; line-height: 1.25; }
  .contacts { list-style: none; margin-top: 8px; }
  .contacts li {
    display: flex; align-items: center; gap: 8px;
    font-size: 13px; line-height: 1.5;
  }
  .contacts svg { width: 13px; height: 13px; flex: none; fill: var(--orange); }
</style>
</head>
<body>
<main class="canvas">
  <section class="card card-back">
    <p class="brand-name">Coastline Premier<br>Retreats</p>
  </section>

  <section class="card card-front">
    <svg class="swoosh" viewBox="0 0 665 380" preserveAspectRatio="none" aria-hidden="true">
      <path d="M0,342 C320,342 580,310 665,170 L665,380 L0,380 Z" fill="var(--ink)"/>
      <path d="M120,330 C390,328 575,290 655,180" fill="none" stroke="var(--orange)" stroke-width="5" stroke-linecap="round"/>
    </svg>

    <p class="brand-name">Coastline Premier<br>Retreats</p>

    <div class="divider"></div>

    <div class="details">
      <h1 class="person-name">Daniel Marsh</h1>
      <p class="role">Co-Founder</p>
      <p class="role">Luxury Hotel &amp; Resort</p>
      <p class="role">Email Marketing</p>
      <ul class="contacts">
        <li>
          <svg viewBox="0 0 16 16" aria-hidden="true"><path d="M3 1h3l1.5 4-2 1.3a9 9 0 0 0 4.2 4.2L11 8.5l4 1.5v3a2 2 0 0 1-2 2A12 12 0 0 1 1 3a2 2 0 0 1 2-2z"/></svg>
          555-201-4417
        </li>
        <li>
          <svg viewBox="0 0 16 16" aria-hidden="true"><path d="M4.5 0h7A1.5 1.5 0 0 1 13 1.5v13a1.5 1.5 0 0 1-1.5 1.5h-7A1.5 1.5 0 0 1 3 14.5v-13A1.5 1.5 0 0 1 4.5 0zM5 2v10h6V2zm3 11a1 1 0 1 0 0 2 1 1 0 0 0 0-2z"/></svg>
          555-309-6128
        </li>
        <li>
          <svg viewBox="0 0 16 16" aria-hidden="true"><path d="M0 3h16v1.2L8 9 0 4.2zM0 5.6l8 4.8 8-4.8V13H0z"/></svg>
          info@coastlinepremierretreats.example
        </li>
        <li>
          <svg viewBox="0 0 16 16" aria-hidden="true"><path d="M8 0a8 8 0 1 0 0 16A8 8 0 0 0 8 0zm0 1.5c.9 0 2 1.8 2.3 5.5H5.7C6 3.3 7.1 1.5 8 1.5zM1.6 9h2.6c.1 1.9.5 3.6 1.1 4.8A6.5 6.5 0 0 1 1.6 9zm0-2a6.5 6.5 0 0 1 3.7-4.8C4.7 3.4 4.3 5.1 4.2 7zm6.4 7.5c-.9 0-2-1.8-2.3-5.5h4.6c-.3 3.7-1.4 5.5-2.3 5.5zm2.7-.7c.6-1.2 1-2.9 1.1-4.8h2.6a6.5 6.5 0 0 1-3.7 4.8zM11.8 7c-.1-1.9-.5-3.6-1.1-4.8A6.5 6.5 0 0 1 14.4 7z"/></svg>
          www.coastlinepremierretreats.example
        </li>
      </ul>
    </div>
  </section>
</main>
</body>
</html>
```